Upmarket Dessert Lounge needs a Business Card Design

We are an upmarket dessert lounge needing a business card to match our image.

We want something that is simple yet beautiful, feminine, classy, sophisticated and elegant. We want it to stand out and don't mind if it is bold.

The design should include our logo and colours of red or maroon with gold highlights. We don't mind if black is used.

Marlow & Quince

Target Market(s)

For those who like to indulge or treat themselves and give in to their temptations on good quality desserts.

Industry/Entity Type

Business

Requirements
Must have
• Must include our logo and our name

Marlow & Quince

M & Q

```html
<!DOCTYPE html>
<html lang="en">
<head>
<meta charset="utf-8">
<title>Marlow &amp; Quince — Business Card</title>
<link rel="stylesheet" href="https://fonts.googleapis.com/css2?family=Libre+Baskerville:wght@400;700&family=Open+Sans:wght@400;600&display=swap">
<style>
  :root {
    --maroon: #7a1416;
    --maroon-deep: #5e0f11;
    --peach: #f7d3a0;
    --cream: #f9d9a8;
    --white: #ffffff;
    --ink: #2d2d2d;
    --backdrop: #ece7e1;
    --serif: "Libre Baskerville", Georgia, serif;
    --sans: "Open Sans", Arial, sans-serif;
  }
  * { box-sizing: border-box; margin: 0; padding: 0; }
  html, body { width: 1200px; height: 758px; overflow: hidden; }
  body { background: var(--backdrop); position: relative; font-family: var(--sans); }

  .card {
    position: absolute; top: 224px;
    width: 540px; height: 310px;
    border-radius: 26px; overflow: hidden;
    box-shadow: 0 10px 28px rgba(0,0,0,.18);
  }
  .card--front { left: 40px; background: var(--white); }
  .card--back  { left: 620px; background: var(--maroon); }

  .card__waves { position: absolute; inset: 0; width: 100%; height: 100%; }

  .brand {
    position: absolute; left: 28px; top: 96px; width: 240px;
    display: flex; align-items: center; gap: 10px;
    font-family: var(--serif); font-weight: 400; font-size: 20px;
    color: var(--maroon); white-space: nowrap;
  }
  .brand__dot { width: 12px; height: 12px; border-radius: 50%; background: var(--maroon); flex: none; }

  .divider {
    position: absolute; left: 286px; top: 40px; width: 1px; height: 140px;
    background: linear-gradient(to bottom, #cfcfcf, #efefef);
  }

  .contact { position: absolute; left: 302px; top: 40px; color: var(--ink); }
  .contact__name { font-family: var(--serif); font-weight: 700; font-size: 17px; color: var(--maroon); }
  .contact__title { font-size: 12px; margin: 2px 0 14px; }
  .contact__list { list-style: none; font-size: 12px; line-height: 18px; }
  .contact__list li { display: flex; align-items: center; gap: 5px; }
  .contact__list svg { width: 10px; height: 10px; fill: var(--ink); flex: none; }

  .address {
    position: absolute; left: 36px; bottom: 28px;
    color: var(--white); font-size: 12.5px; line-height: 19px;
  }

  .monogram {
    position: absolute; left: 0; right: 0; top: 86px; text-align: center;
    font-family: var(--serif); font-weight: 400; font-size: 66px; color: var(--cream);
    letter-spacing: 2px;
  }
  .web {
    position: absolute; left: 0; right: 0; bottom: 50px; text-align: center;
    color: var(--white); font-size: 19px; letter-spacing: 3px;
  }
</style>
</head>
<body>
  <section class="card card--front" aria-label="Card front">
    <svg class="card__waves" viewBox="0 0 540 310" preserveAspectRatio="none" aria-hidden="true">
      <path d="M0,232 C190,230 400,214 540,150 L540,310 L0,310 Z" fill="var(--maroon)"/>
      <path d="M110,234 C300,226 440,200 540,158 L540,176 C430,214 290,232 110,234 Z" fill="var(--peach)"/>
      <path d="M150,232 C320,222 450,192 540,140 L540,150 C440,200 310,224 150,232 Z" fill="var(--maroon-deep)"/>
    </svg>

    <div class="brand"><span class="brand__dot"></span>Marlow &amp; Quince</div>
    <div class="divider"></div>

    <div class="contact">
      <p class="contact__name">Your name</p>
      <p class="contact__title">Title</p>
      <ul class="contact__list">
        <li><svg viewBox="0 0 10 10"><path d="M2 0.5 L4 2.6 L3 3.6 Q4 6 6.4 7 L7.4 6 L9.5 8 L8.3 9.5 Q3.5 9 0.5 1.7 Z"/></svg>555-014-2290</li>
        <li><svg viewBox="0 0 10 10"><path d="M3 0 H7 V10 H3 Z M3.8 1 V7.5 H6.2 V1 Z"/></svg>555-014-2290</li>
        <li><svg viewBox="0 0 10 10"><path d="M0 2 H10 V8.5 H0 Z M0.6 2.4 L5 5.6 L9.4 2.4"/></svg>info@marlowquince.com</li>
        <li><svg viewBox="0 0 10 10"><circle cx="5" cy="5" r="4.6"/></svg>www.marlowquince.com</li>
      </ul>
    </div>

    <p class="address">Street Name, City Name<br>State Zip Code</p>
  </section>

  <section class="card card--back" aria-label="Card back">
    <p class="monogram">M &amp; Q</p>
    <p class="web">www.marlowquince.com</p>
  </section>
</body>
</html>
```